International IT business needs website revamp.

Velmor Limited would like their current website (www.velmorlimited-example.com) to be revamped/modernized to reflect up-to-date goods and services. Currently, Velmor is offering a conversational AI workflow platform for both enterprise clients and as a DIY solution for SMBs. This platform is called tqFlowbin and allows organizations to automate simple and repetitive workflows to drive their operational efficiency. In addition to the solution offering, Velmor Limited also provides professional IT services. With that said, please use www.velmorlimited-example.com and www.tqflowbin-example.ai for reference of current logos and colourways desired. Furthermore, refer to the attached PDF for a general idea of what to include in the site. The final design should be easy to navigate, clear, concise, and emphasize tqFlowbin as a solution for enterprise clients (while redirecting SMBs to the tqFlowbin website) looking to automate workflow processes/kickstart their digital transformation journey.

```html
<!DOCTYPE html>
<html lang="en">
<head>
<meta charset="utf-8">
<title>Velmor Limited</title>
<link href="https://fonts.googleapis.com/css2?family=Montserrat:wght@400;500;600;700&family=Open+Sans:wght@400;600&display=swap" rel="stylesheet">
<style>
:root{
  --blue:#3a9ad9;
  --blue-dark:#2d86c4;
  --band:#8fcbeb;
  --teal:#5ec2ae;
  --ink:#1f2a33;
  --muted:#5b6670;
  --line:#e3e7ea;
  --footer:#1c1d20;
  --footer-line:#33353a;
  --white:#ffffff;
}
*{margin:0;padding:0;box-sizing:border-box}
html,body{width:1200px;height:2812px;overflow:hidden}
body{position:relative;background:var(--white);font-family:"Open Sans",Arial,sans-serif;color:var(--ink)}
h1,h2,h3,.nav,.btn,.brand{font-family:"Montserrat",Arial,sans-serif}
.abs{position:absolute}

/* header */
.site-header{left:0;top:0;width:1200px;height:100px;display:flex;align-items:center;justify-content:space-between;padding:0 110px}
.brand{display:flex;align-items:center;gap:10px;font-weight:700;font-size:30px;color:var(--ink)}
.brand-dot{width:14px;height:14px;border-radius:50%;background:var(--blue)}
.nav{display:flex;gap:44px;font-size:17px;font-weight:500}
.nav a{color:var(--ink);text-decoration:none}
.nav a.active{color:var(--blue)}

/* hero */
.hero{left:0;top:100px;width:1200px;height:400px;background:linear-gradient(120deg,#8a6f5c 0%,#c9b6a2 35%,#e9e4dc 60%,#9e8a78 100%)}
.hero .brand{position:absolute;right:110px;top:70px;color:var(--white);font-size:44px}
.hero .brand-dot{width:18px;height:18px;background:var(--white)}

.section-title{font-size:26px;font-weight:600;color:var(--ink)}
.small-text{font-size:14px;line-height:1.55;color:var(--muted)}

/* clients / partners */
.logo-row{display:flex;gap:20px}
.logo-tile{width:160px;height:110px;border:1px solid var(--line);display:flex;align-items:center;justify-content:center;font-family:"Montserrat",sans-serif;font-weight:700;font-size:24px;color:var(--ink);box-shadow:0 2px 6px rgba(0,0,0,.06)}
.pager{display:flex;gap:10px;font-size:14px;color:var(--muted)}

/* testimonials */
.testimonial{left:120px;width:960px;background:var(--band);padding:80px 70px 32px}
.testimonial-tab{position:absolute;left:0;top:0;background:var(--white);padding:14px 26px 14px 22px;border-left:6px solid var(--blue)}
.testimonial-tab h2{font-size:24px;font-weight:600}
.testimonial blockquote{font-size:15px;line-height:1.7;color:var(--ink)}
.testimonial cite{display:block;margin-top:18px;font-style:normal;font-weight:700;font-family:"Montserrat",sans-serif;font-size:16px}

.btn{display:inline-block;background:var(--blue);color:var(--white);font-size:13px;font-weight:600;padding:11px 26px;border-radius:22px;letter-spacing:.5px}

/* core team */
.team-photo{left:490px;top:1150px;width:340px;height:240px;background:linear-gradient(135deg,#b9cfe0,#eef2f5 55%,#8aa4b8)}
.stat{width:240px;padding:22px 24px;color:var(--white)}
.stat strong{display:block;font-family:"Montserrat",sans-serif;font-size:34px;font-weight:700}
.stat span{font-size:13px}
.stat-teal{background:var(--teal)}
.stat-blue{background:var(--blue-dark)}
.stat-icon{width:34px;height:34px;margin-bottom:8px}

/* videos */
.video-thumb{height:180px;display:flex;align-items:center;justify-content:center}
.play{width:56px;height:56px}

/* footer */
.site-footer{left:0;top:2440px;width:1200px;height:372px;background:var(--footer);color:#d8dadd}
.site-footer .brand{color:var(--white)}
.footer-nav{display:flex;gap:40px;font-family:"Montserrat",sans-serif;font-size:16px;color:var(--white)}
.footer-col{font-size:14px;line-height:1.6;display:flex;gap:14px}
.footer-col svg{flex:none;width:20px;height:20px;margin-top:2px}
.footer-bottom{left:0;top:320px;width:1200px;height:52px;border-top:1px solid var(--footer-line);display:flex;align-items:center;justify-content:space-between;padding:0 110px;font-size:13px;color:#9a9ea4}
.product-tag{font-family:"Montserrat",sans-serif;font-weight:600;color:var(--blue);font-size:14px}
.contact-tab{right:0;top:2500px;width:46px;height:180px;background:var(--teal);border-radius:14px 0 0 14px;display:flex;align-items:center;justify-content:center}
.contact-tab span{transform:rotate(-90deg);white-space:nowrap;color:var(--white);font-size:13px;font-family:"Montserrat",sans-serif;font-weight:600}
</style>
</head>
<body>

<header class="site-header abs">
  <div class="brand"><span class="brand-dot"></span>Velmor</div>
  <nav class="nav">
    <a class="active" href="#">Home</a><a href="#">About Us</a><a href="#">Services</a><a href="#">Products</a><a href="#">Contact Us</a>
  </nav>
</header>

<section class="hero abs" role="img" aria-label="Team meeting around a table in a bright brick-walled office">
  <div class="brand"><span class="brand-dot"></span>Velmor</div>
</section>

<section class="abs" style="left:110px;top:560px;width:240px">
  <h2 class="section-title">Clients</h2>
  <p class="small-text" style="margin-top:10px">Velmor's current clientele consists of businesses from many sectors including Advertising, Financial and Telecommunications companies.</p>
</section>
<div class="logo-row abs" style="left:370px;top:560px">
  <div class="logo-tile">Belmark</div>
  <div class="logo-tile">Merrow</div>
  <div class="logo-tile">Onyra</div>
  <div class="logo-tile">Cavra</div>
</div>
<div class="pager abs" style="left:1050px;top:690px">‹ ›</div>

<section class="testimonial abs" style="top:750px">
  <div class="testimonial-tab"><h2>Testimonials</h2></div>
  <blockquote>"Leveraging Velmor's extremely user-friendly interface, Service Northland was able to build and implement our own bot for the Service Desk Account (SDA) page without the assistance of Velmor developers. By removing the need for programmers, we are able to make adjustments to our bot instantaneously!"</blockquote>
  <cite>– Service Northland</cite>
</section>

<section class="abs" style="left:110px;top:1140px;width:350px">
  <h2 class="section-title" style="font-size:30px;line-height:1.25">A core team that has worked together for Over 15 years</h2>
  <p class="small-text" style="margin-top:18px">Velmor is customer-centric, identifying and delivering flexible solutions that make the best sense to the customers.</p>
  <span class="btn" style="margin-top:22px">ABOUT US</span>
</section>
<div class="team-photo abs" role="img" aria-label="Two business people shaking hands at an office desk"></div>
<div class="stat stat-teal abs" style="left:850px;top:1100px">
  <svg class="stat-icon" viewBox="0 0 34 34"><rect x="4" y="8" width="26" height="22" fill="none" stroke="#fff" stroke-width="2.5"/><line x1="4" y1="14" x2="30" y2="14" stroke="#fff" stroke-width="2.5"/></svg>
  <strong>2011estd.</strong><span>Velmor was launched in the summer of 2011</span>
</div>
<div class="stat stat-blue abs" style="left:850px;top:1270px">
  <strong>20+</strong><span>Over 20 consultants and business partners</span>
</div>

<section class="testimonial abs" style="top:1440px">
  <div class="testimonial-tab"><h2>Testimonials</h2></div>
  <blockquote>"Our company, Forward Structures, was able to deploy our website chatbot within one month! We were extremely satisfied with tqFlowbin, as we are discussing the introduction of a new capability to our bot. This capability will allow the bot to proactively reach out to clients, provide before and after sales support, and maintain positive relations to capture additional sales by retaining customers!"</blockquote>
  <cite>– Forward Structures</cite>
</section>

<section class="abs" style="left:110px;top:1760px;width:360px">
  <h2 class="section-title" style="font-size:30px">Promotional Videos</h2>
  <p class="small-text" style="margin-top:14px">Velmor is customer-centric, identifying and delivering flexible solutions that make the best sense to the customers.</p>
  <span class="btn" style="margin-top:20px">MORE VIDEOS</span>
</section>
<div class="video-thumb abs" style="left:560px;top:1750px;width:240px;background:linear-gradient(135deg,#3c4a58,#8b98a6)" role="img" aria-label="Video still of a speaker at a conference">
  <svg class="play" viewBox="0 0 56 56"><circle cx="28" cy="28" r="27" fill="#fff"/><path d="M23 18 L38 28 L23 38Z" fill="#1f2a33"/></svg>
</div>
<div class="video-thumb abs" style="left:820px;top:1750px;width:270px;background:linear-gradient(135deg,#6d7f8f,#c7d2db)" role="img" aria-label="Video still of a team at a whiteboard">
  <svg class="play" viewBox="0 0 56 56"><circle cx="28" cy="28" r="27" fill="#fff"/><path d="M23 18 L38 28 L23 38Z" fill="#1f2a33"/></svg>
</div>

<section class="abs" style="left:110px;top:1990px;width:240px">
  <h2 class="section-title">Partners</h2>
  <p class="small-text" style="margin-top:10px">Velmor works with trusted partners across the technology, retail, consumer and finance industries.</p>
</section>
<div class="logo-row abs" style="left:370px;top:1990px">
  <div class="logo-tile">Kestra</div>
  <div class="logo-tile">Vantor</div>
  <div class="logo-tile">Welnor</div>
  <div class="logo-tile">Paxel</div>
</div>
<div class="pager abs" style="left:1050px;top:2112px">‹ ›</div>

<section class="testimonial abs" style="top:2150px">
  <div class="testimonial-tab"><h2>Testimonials</h2></div>
  <blockquote>"Naturally, the Passage Bureau website receives thousands of visitors a day. As a result, we noticed the need to automate simple and repetitive questions to provide quick, on-demand assistance while maximizing our worker productivity without compromising costs. They we enlisted Velmor and their chatbot solution to accomplish the task. Since launching, the Passage Bureau bot in Q2 2019, we have achieved over 78% of inquiries being automatically answered successfully!"</blockquote>
  <cite>– Passage Bureau</cite>
</section>

<footer class="site-footer abs">
  <div class="brand abs" style="left:110px;top:40px"><span class="brand-dot"></span>Velmor</div>
  <nav class="footer-nav abs" style="right:110px;top:50px"><span>Home</span><span>About Us</span><span>Services</span><span>Products</span><span>Contact Us</span></nav>
  <div class="abs" style="left:110px;top:108px;width:980px;height:1px;background:var(--footer-line)"></div>

  <div class="footer-col abs" style="left:110px;top:138px;width:230px">
    <svg viewBox="0 0 20 20"><path d="M10 1a6 6 0 0 0-6 6c0 5 6 12 6 12s6-7 6-12a6 6 0 0 0-6-6z" fill="none" stroke="#d8dadd" stroke-width="1.6"/><circle cx="10" cy="7" r="2" fill="#d8dadd"/></svg>
    <p>Velmor Ltd.<br>418 Harlow Avenue,<br>Suite 7,<br>Brookfield, ON<br>K2P 0B4</p>
  </div>
  <div class="footer-col abs" style="left:400px;top:138px;width:280px">
    <svg viewBox="0 0 20 20"><path d="M10 1a6 6 0 0 0-6 6c0 5 6 12 6 12s6-7 6-12a6 6 0 0 0-6-6z" fill="none" stroke="#d8dadd" stroke-width="1.6"/><circle cx="10" cy="7" r="2" fill="#d8dadd"/></svg>
    <p>Velmor (HK) Limited,<br>Office 1502, 15th Floor,<br>Harbourline Centre,<br>78 Quay Road, Eastpoint,<br>Hong Kong</p>
  </div>
  <div class="abs" style="left:740px;top:138px;width:360px;display:flex;flex-direction:column;gap:20px">
    <div class="footer-col"><svg viewBox="0 0 20 20"><rect x="1.5" y="4" width="17" height="12" fill="none" stroke="#d8dadd" stroke-width="1.6"/><path d="M2 5l8 6 8-6" fill="none" stroke="#d8dadd" stroke-width="1.6"/></svg><p>Email: info@velmorlimited-example.com</p></div>
    <div class="footer-col"><svg viewBox="0 0 20 20"><path d="M5 2l3 4-2 2c1 2 3 4 5 5l2-2 4 3-2 3C9 17 3 11 2 4z" fill="none" stroke="#d8dadd" stroke-width="1.6"/></svg><p>+1 (555) 010-2481<br>+1 (555) 010-7730 (for outside Toronto)</p></div>
    <div class="footer-col"><svg viewBox="0 0 20 20"><circle cx="10" cy="10" r="8" fill="none" stroke="#d8dadd" stroke-width="1.6"/><path d="M10 5v5l3 2" fill="none" stroke="#d8dadd" stroke-width="1.6"/></svg><p>Weekdays: 9:00am to 5:30pm<br>Weekends: Closed</p></div>
  </div>

  <div class="footer-bottom abs">
    <span>© 2020 | www.velmorlimited-example.com</span>
    <span class="product-tag">tqFlowbin</span>
  </div>
</footer>

<div class="contact-tab abs"><span>Get in touch</span></div>

</body>
</html>
```